Business Card Design Project

This is to go hand in hand with our stationery project.
Target Market(s)
Business Professionals in the Finance, HR and C-Level management arena. They are global companies that run enterprise technology solutions/products.
Mostly Male, mid 30's to 60's.
Industry/Entity Type
Business
Font styles to use
Other font styles liked:
- Calibri
Colors
9bcb3c
000000
1b1b1b
c4c4c4
ffffff
Requirements
Must have
- Logo
Name, title, contact details, address on the front of the card.
ABN and web address need to be on the card, along with our tag line
See | Share | Do
We also require rounded corners and for the card to be landscape please.
Our green is
C98 M0 Y93 K0
Modern, contemporary and must have white space for people to write on.
Nice to have
- Consistent elements with the stationery design.
Should not have
- No 90's waves - We want the feeling of movement but no wavey lines.

```html
<!DOCTYPE html>
<html lang="en">
<head>
<meta charset="utf-8">
<title>Veltra Business Solutions – Business Card</title>
<link href="https://fonts.googleapis.com/css2?family=Carlito:wght@400;700&display=swap" rel="stylesheet">
<style>
  :root {
    --green: #9bcb3c;
    --black: #000000;
    --ink: #1b1b1b;
    --grey: #c4c4c4;
    --tag-grey: #a9a9a9;
    --white: #ffffff;
    --stage: #2f2b28;
    --dark-top: #6b6968;
    --dark-base: #2c2c2c;
  }
  * { margin: 0; padding: 0; box-sizing: border-box; }
  html, body { width: 1000px; height: 1200px; overflow: hidden; }
  body {
    background: var(--stage);
    font-family: "Carlito", "Calibri", sans-serif;
    position: relative;
  }
  .card {
    position: absolute;
    width: 720px;
    height: 436px;
    border-radius: 28px;
    overflow: hidden;
    background: var(--white);
  }

  /* Front */
  .card--front { left: 141px; top: 120px; }
  .brand {
    position: absolute; left: 44px; top: 52px;
    display: flex; align-items: center; gap: 12px;
  }
  .brand__dot { width: 22px; height: 22px; border-radius: 50%; background: var(--green); }
  .brand__name {
    font-weight: 700; font-size: 30px; line-height: 1.05; color: var(--ink);
  }
  .abn { position: absolute; left: 55px; top: 167px; font-size: 17px; color: var(--ink); }
  .person { position: absolute; right: 45px; top: 64px; text-align: right; color: var(--black); }
  .person__name { font-weight: 700; font-size: 31px; line-height: 1.1; }
  .person__title { font-size: 23px; line-height: 1.2; }
  .contacts { position: absolute; left: 52px; top: 238px; list-style: none; color: var(--ink); font-size: 21px; }
  .contacts li { display: flex; align-items: flex-start; gap: 9px; height: 30.5px; line-height: 26px; }
  .contacts li.address { margin-top: 14px; height: auto; }
  .contacts svg { width: 19px; height: 19px; margin-top: 4px; flex: none; fill: var(--green); }
  .tagline--front {
    position: absolute; right: 44px; bottom: 38px;
    font-size: 35px; color: var(--tag-grey); letter-spacing: 0.5px;
  }
  .tagline .sep { color: var(--green); font-size: 0.6em; vertical-align: middle; margin: 0 6px; }
  .card--front .edge-band { position: absolute; left: 0; right: 0; bottom: 0; height: 20px; background: var(--green); }

  /* Back */
  .card--back { left: 126px; top: 638px; }
  .back-panel {
    position: absolute; left: 0; top: 0; right: 0; height: 290px;
    background: radial-gradient(ellipse 60% 95% at 52% 0%, var(--dark-top), var(--dark-base) 90%);
    text-align: center; color: var(--white);
  }
  .back-panel__name { padding-top: 82px; font-weight: 700; font-size: 62px; line-height: 1; letter-spacing: 1px; }
  .back-panel__sub { font-size: 31px; margin-top: 34px; line-height: 1; }
  .tagline--back { font-weight: 700; font-size: 23px; line-height: 1.2; color: var(--grey); margin-top: 10px; }
  .back-panel__web { font-weight: 700; font-size: 19px; line-height: 1.2; letter-spacing: 2px; color: var(--green); margin-top: 10px; }
  .back-rule { position: absolute; left: 0; right: 0; top: 290px; height: 4px; background: var(--green); }
</style>
</head>
<body>

<section class="card card--front" aria-label="Card front">
  <div class="brand">
    <span class="brand__dot"></span>
    <span class="brand__name">Veltra<br>Business Solutions</span>
  </div>
  <p class="abn">ABN 00 000 000 000</p>

  <div class="person">
    <p class="person__name">Daniel Hartley</p>
    <p class="person__title">Manager</p>
  </div>

  <ul class="contacts">
    <li>
      <svg viewBox="0 0 24 24" aria-hidden="true"><path d="M6.6 10.8a15.1 15.1 0 0 0 6.6 6.6l2.2-2.2a1 1 0 0 1 1-.25 11.4 11.4 0 0 0 3.6.57 1 1 0 0 1 1 1V20a1 1 0 0 1-1 1A17 17 0 0 1 3 4a1 1 0 0 1 1-1h3.5a1 1 0 0 1 1 1c0 1.25.2 2.450.57 3.57a1 1 0 0 1-.25 1z"/></svg>
      <span>+61 (02) 5550 1842</span>
    </li>
    <li>
      <svg viewBox="0 0 24 24" aria-hidden="true"><path d="M6 2h9l3 3v5H6z M3 11h18v11H3z M7 14v2h10v-2z M7 18v2h6v-2z"/></svg>
      <span>+61 (02) 5550 1843</span>
    </li>
    <li>
      <svg viewBox="0 0 24 24" aria-hidden="true"><path d="M2 5h20v14H2z M3.5 6.5 12 13l8.5-6.5" stroke="#fff" stroke-width="1.6"/></svg>
      <span>sales@veltrabusiness.com</span>
    </li>
    <li class="address">
      <svg viewBox="0 0 24 24" aria-hidden="true"><path d="M12 2a7 7 0 0 0-7 7c0 5.2 7 13 7 13s7-7.8 7-13a7 7 0 0 0-7-7zm0 9.5A2.5 2.5 0 1 1 12 6.5a2.5 2.5 0 0 1 0 5z"/></svg>
      <span>Level 7, 22 Harbour Lane,<br>Eastwood, NSW 2122</span>
    </li>
  </ul>

  <p class="tagline tagline--front">Plan<span class="sep">●</span>Build<span class="sep">●</span>Grow</p>
  <div class="edge-band"></div>
</section>

<section class="card card--back" aria-label="Card back">
  <div class="back-panel">
    <p class="back-panel__name">Veltra</p>
    <p class="back-panel__sub">Business Solutions</p>
    <p class="tagline tagline--back">Plan<span class="sep">●</span>Build<span class="sep">●</span>Grow</p>
    <p class="back-panel__web">www.veltrabusiness.com</p>
  </div>
  <div class="back-rule"></div>
</section>

</body>
</html>
```